QP Fiduciary Website Redesign Contest

We want to refresh our website to be more insitutional, professional for an international audience. We have designed a new logo for this purpose and that has been attached. A full brand brief and positioning statement has also been attached. Please read through all the documents carefully before designing. The old website is found here: https://qp-fiduciary.example/

Target Market(s)

Actuaries and associated businesses internationally

Industry/Entity Type

professional services - actuaries

Number of Pages Required

3 page

Font styles to use
Sans Serif

Colors
0054AA
0677BA
7BADD7
CADEEF
E8F1F8
0094D4
00A9DD
6FCCEA
C7EBF8
E9F6FB
F0912C
F2A743
F7CA91
FBE8D2
FDF5EE
EE7325
F08F49
F5BC92
FAE3D3
FDF4ED
EB3D1F
EC4F4E
F09395
F8D3D4
FCEDEE

Requirements
Must have
• blues and greens to match the logo color, complimentary colors, navigation
Nice to have
• old site: https://qp-fiduciary.example/

```html
<!DOCTYPE html>
<html lang="en">
<head>
<meta charset="utf-8">
<title>QP Fiduciary — Actuarial Software</title>
<link rel="stylesheet" href="https://fonts.googleapis.com/css2?family=Michroma&family=Outfit:wght@400;500;600;700&display=swap">
<style>
:root{
  --ink:#111318;
  --text:#2a2d35;
  --muted:#b9bcc4;
  --orange:#f97a0a;
  --blue:#0b4ff0;
  --teal:#00cdbd;
  --green:#10a56f;
  --hero-tint:#e7e8fb;
  --white:#ffffff;
  --black:#050505;
  --rule:#e4e6ea;
  --diagram-soft:#f1f2f6;
  --diagram-peach:#fbe3cc;
}
*{box-sizing:border-box;margin:0;padding:0}
html,body{width:1200px;height:3100px;overflow:hidden;background:var(--white)}
body{position:relative;font-family:"Outfit",sans-serif;color:var(--text)}
a{text-decoration:none}
.display{font-family:"Michroma",sans-serif;color:var(--ink);text-transform:uppercase;font-weight:400}
.btn{position:absolute;display:flex;align-items:center;justify-content:center;background:var(--orange);color:var(--white);font-family:"Outfit",sans-serif;font-weight:700;font-size:12px;text-transform:uppercase;letter-spacing:.2px}
.wordmark{position:absolute;font-family:"Outfit",sans-serif;font-weight:600;color:var(--ink);letter-spacing:1px;display:flex;align-items:center;gap:10px;white-space:nowrap}
.wordmark .dot{width:14px;height:14px;border-radius:50%;background:var(--orange)}

/* header */
.site-header{position:absolute;left:0;top:0;width:1200px;height:82px;background:var(--white)}
.site-header .wordmark{left:112px;top:22px;font-size:28px}
.main-nav{position:absolute;top:0;left:436px;height:82px}
.main-nav a{position:absolute;top:35px;font-size:11.5px;font-weight:600;color:var(--ink);white-space:nowrap}
.main-nav a.active{color:var(--teal)}
.main-nav a.active::before{content:"";position:absolute;left:0;right:0;top:-35px;height:2px;background:var(--teal)}
.site-header .btn{left:915px;top:19px;width:172px;height:44px}

/* hero */
.hero{position:absolute;left:0;top:82px;width:1200px;height:628px;background:linear-gradient(180deg,var(--hero-tint) 0%,#f6f6fd 70%,var(--white) 100%)}
.hero-waves{position:absolute;inset:0}
.hero h1{position:absolute;left:112px;top:105px;font-size:35px;line-height:41.5px;letter-spacing:2px;white-space:nowrap}
.hero .lede{position:absolute;left:112px;top:280px;width:425px;font-size:13.5px;line-height:19px}
.hero .btn{left:112px;top:336px;width:271px;height:43px}
.hero .scroll-hex{position:absolute;left:854px;top:500px}

/* overview */
.overview-diagram{position:absolute;left:120px;top:785px;width:506px;height:223px;background:var(--diagram-soft);border-radius:4px}
.overview-copy{position:absolute;left:650px;top:800px;width:440px}
.overview-copy h2{font-size:23px;letter-spacing:1px;white-space:nowrap}
.overview-copy p{margin-top:20px;font-size:13.5px;line-height:19px}
.overview-copy .btn{left:0;top:117px;width:153px;height:39px}

/* core solutions */
.solutions{position:absolute;left:0;top:1087px;width:1200px;height:458px;background:var(--blue)}
.solutions h2{position:absolute;left:0;right:0;top:75px;text-align:center;color:var(--white);font-size:25px;letter-spacing:1px}
.solution-card{position:absolute;top:133px;width:281px;height:233px;background:var(--white);text-align:center}
.solution-card .hex{margin:26px auto 0;display:block}
.solution-card h3{margin-top:12px;font-size:13.5px;font-weight:600;color:var(--ink);text-transform:uppercase}
.solution-card p{margin:10px auto 0;width:230px;font-size:13px;line-height:19px}

/* characteristics */
.characteristics{position:absolute;left:190px;top:1722px;width:420px}
.characteristics h2{font-size:21px;line-height:30px;letter-spacing:1px}
.characteristics ul{list-style:none;margin-top:22px}
.characteristics li{position:relative;padding-left:19px;font-size:13.5px;line-height:26.5px;white-space:nowrap}
.characteristics li::before{content:"";position:absolute;left:1px;top:8px;width:10px;height:10px;border-radius:50%;background:var(--green);box-shadow:0 0 0 1.5px var(--ink)}
.process-diagram{position:absolute;left:642px;top:1608px;width:373px;height:391px;background:linear-gradient(160deg,var(--diagram-soft),var(--diagram-peach));border-radius:4px}

/* insights */
.insights h2{position:absolute;left:0;right:0;top:2078px;text-align:center;font-size:23px;letter-spacing:1px}
.insight{position:absolute;top:2132px;width:312px}
.insight .thumb{height:228px;position:relative}
.insight .tag{position:absolute;left:16px;top:16px;background:var(--white);color:var(--ink);font-size:9px;font-weight:700;padding:6px 12px}
.insight time{display:block;margin-top:17px;text-align:center;font-size:11px;color:var(--muted)}
.insight h3{margin-top:9px;text-align:center;font-size:12.5px;line-height:19px;font-weight:600;color:var(--ink);text-transform:uppercase}
.insights .btn{left:535px;top:2471px;width:131px;height:38px}

/* cta */
.cta{position:absolute;left:0;top:2598px;width:1200px;height:163px;background:linear-gradient(90deg,#ff8a00 0%,#fba01a 45%,#ff8f0a 75%,#fb6d10 100%)}
.cta h2{position:absolute;left:112px;top:55px;color:var(--white);font-size:25px;line-height:34px;letter-spacing:1px}
.cta .btn{left:827px;top:63px;width:260px;height:38px;background:var(--white);color:var(--ink);font-size:11px}

/* footer */
.site-footer{position:absolute;left:0;top:2761px;width:1200px;height:293px;background:var(--white)}
.site-footer .wordmark{left:112px;top:105px;font-size:28px}
.footer-col{position:absolute;top:96px;height:152px;border-left:1px solid var(--rule);padding-left:39px}
.footer-col h4{font-family:"Michroma",sans-serif;font-weight:400;font-size:13px;color:var(--ink);text-transform:uppercase}
.footer-col a{display:block;margin-top:13px;font-size:12.5px;color:var(--text)}
.footer-col h4+a{margin-top:16px}
.legal-bar{position:absolute;left:0;top:3054px;width:1200px;height:46px;background:var(--black);color:var(--white);font-size:12.5px;display:flex;align-items:center;justify-content:center}
.legal-bar .social{position:absolute;left:1064px;top:12px;width:22px;height:22px;border-radius:50%;background:var(--white)}
</style>
</head>
<body>

<header class="site-header">
  <a class="wordmark" href="https://qp-fiduciary.example/"><span class="dot"></span>QP FIDUCIARY</a>
  <nav class="main-nav">
    <a class="active" style="left:0">HOME</a>
    <a style="left:61px">PLATFORM</a>
    <a style="left:149px">SOLUTIONS</a>
    <a style="left:241px">INSIGHTS</a>
    <a style="left:320px">COMPANY</a>
    <a style="left:404px">CONTACT</a>
  </nav>
  <a class="btn" href="#">Request Technical</a>
</header>

<section class="hero">
  <div class="hero-waves" role="img" aria-label="Flowing fine-line wave ribbon sweeping across the hero background"></div>
  <h1 class="display">Actuarial Software<br>,For Structured<br>Auditable Financial<br>Analysis</h1>
  <p class="lede">Software that translates actuarial methodologies into disciplined decision-ready analytical tools across diverse regulatory environment</p>
  <a class="btn" href="#">Request a Technical Walkthrough</a>
  <svg class="scroll-hex" width="87" height="100" viewBox="0 0 87 100" aria-hidden="true">
    <polygon points="43.5,0 87,25 87,75 43.5,100 0,75 0,25" fill="var(--black)"/>
    <path d="M43.5 38 V62 M34 53 L43.5 62 L53 53" stroke="#fff" stroke-width="2" fill="none"/>
  </svg>
</section>

<section class="overview">
  <div class="overview-diagram" role="img" aria-label="Order process flow diagram from customer order through payment to shipping"></div>
  <div class="overview-copy">
    <h2 class="display">Platform Overview</h2>
    <p>QP Fiduciary develops modular actuarial software designed to supportreserving, valuation, pricing, and risk analysis workflows across diverse regulatory environments</p>
    <a class="btn" href="#">Explore Platform</a>
  </div>
</section>

<section class="solutions" role="img" aria-label="Blue band with large soft geometric arc pattern">
  <h2 class="display">Core Solutions</h2>
  <article class="solution-card" style="left:156px">
    <svg class="hex" width="72" height="80" viewBox="0 0 72 80" role="img" aria-label="Platform icon"><polygon points="36,0 72,20 72,60 36,80 0,60 0,20" fill="var(--black)"/></svg>
    <h3>Explore Platform</h3>
    <p>Software supporting structured reserving workflows &amp; financial repor ting across jurisdictions.</p>
  </article>
  <article class="solution-card" style="left:460px">
    <svg class="hex" width="72" height="80" viewBox="0 0 72 80" role="img" aria-label="Pricing icon"><polygon points="36,0 72,20 72,60 36,80 0,60 0,20" fill="#13b39a"/></svg>
    <h3>Pricing</h3>
    <p>Models supporting insurance &amp; reinsurance pricing based actuarial methodologies.</p>
  </article>
  <article class="solution-card" style="left:763px">
    <svg class="hex" width="72" height="80" viewBox="0 0 72 80" role="img" aria-label="Risk management icon"><polygon points="36,0 72,20 72,60 36,80 0,60 0,20" fill="var(--black)"/></svg>
    <h3>Enterprise Risk Manage</h3>
    <p style="width:210px">Software supporting reinsurance optimization &amp; capital modeling.</p>
  </article>
</section>

<section>
  <div class="characteristics">
    <h2 class="display">Platform<br>Characteristics</h2>
    <ul>
      <li>Structured workflows suitable for multi-jurisdictional review.</li>
      <li>Transparent assumptions and methodological clarity.</li>
      <li>Comparative scenario analysis.</li>
      <li>Supports professional judgment rather than replacing it.</li>
    </ul>
  </div>
  <div class="process-diagram" role="img" aria-label="Flowchart of a capture, compare and report workflow with decision branch"></div>
</section>

<section class="insights">
  <h2 class="display">Our Insights</h2>
  <article class="insight" style="left:119px">
    <div class="thumb" role="img" aria-label="Blue abstract flowing-line artwork" style="background:linear-gradient(135deg,#1f6bff,#0a46ea 60%,#1257f5)"><span class="tag">ARTICLE</span></div>
    <time>25-01-2026</time>
    <h3>Methodological Perspectives in<br>Actuarial Reserving</h3>
  </article>
  <article class="insight" style="left:444px">
    <div class="thumb" role="img" aria-label="Teal abstract line texture artwork" style="background:linear-gradient(135deg,#07d8c6,#00ccba)"><span class="tag">ARTICLE</span></div>
    <time>11-02-2026</time>
    <h3>Governance Considerations Multi<br>Jurisdictional Analysis</h3>
  </article>
  <article class="insight" style="left:769px">
    <div class="thumb" role="img" aria-label="Orange abstract wave texture artwork" style="background:linear-gradient(135deg,#ff9d10,#ff8a05 60%,#ffa21a)"><span class="tag">ARTICLE</span></div>
    <time>17-03-2026</time>
    <h3>Observations on Actuarial Practice<br>in Emerging Markets</h3>
  </article>
  <a class="btn" href="#">Read Insight</a>
</section>

<section class="cta" role="img" aria-label="Orange band with soft geometric arc pattern">
  <h2 class="display">Interested in Exploring<br>the Platform?</h2>
  <a class="btn" href="#">Request Technical Walkthrough</a>
</section>

<footer class="site-footer">
  <a class="wordmark" href="https://qp-fiduciary.example/"><span class="dot"></span>QP FIDUCIARY</a>
  <div class="footer-col" style="left:398px"><h4>Company</h4><a>About</a><a>Team</a></div>
  <div class="footer-col" style="left:569px"><h4>Platform</h4><a>Overview</a><a>Technology</a></div>
  <div class="footer-col" style="left:743px"><h4>Solutions</h4><a>Reserving</a><a>Pricing</a><a>Enterprise Risk</a></div>
  <div class="footer-col" style="left:923px"><h4>Legal</h4><a>Terms and Condition</a><a>Privacy Policy</a></div>
</footer>
<div class="legal-bar">© QP Fiduciary. All rights reserved.<span class="social" aria-label="Social profile"></span></div>

</body>
</html>
```